KAJU Freightways #ALLKAJU Business Cards & Letterhead

I am looking to business cards designed for our organization. We are currently undergoing a small re-branding that is taking place. Our organization is called KAJU Freightways and we are headquartered in Phoenix, AZ. We primarily provide transportation and logistics services to the Marlow Parcel Bureau who is our largest customer. I would like to see a design that incorporates name, title, contact info, website, and address (this will be different depending on the employee). I would also like to see some color on the business card using our logo colors or a variation. I would like our logo on the back of the business card with the website displayed. The final design should communicate that we are a next generation transportation operate that focuses on being driver-first, customer-centric, innovative, and sustainable.We would also like our #ALLKAJU catch phrase incorporated as well.

Target Market(s)

Transportation & Logistics

Industry/Entity Type

Trucking Company

Contact Information for Business Card

-First and Last Name
-Position Title
-Contact Phone
-Contact Email
-Physical Address

Font styles to use
Serif

Colors

Designer to choose colors to be used in the design.

Requirements
Must have
• -KAJU logo prominently displayed
• -#ALLKAJU catch phrase used
• -Some amount of color, design gradient, etc.
• -Logo on the back with website listed (https://www.kajufreightco.example)

```html
<!DOCTYPE html>
<html lang="en">
<head>
<meta charset="utf-8">
<title>KAJU Freightways — Business Cards</title>
<link href="https://fonts.googleapis.com/css2?family=Montserrat:wght@400;500;600;700;800&display=swap" rel="stylesheet">
<style>
  :root {
    --backdrop: #2a2d31;
    --teal-deep: #0f3440;
    --teal-mid: #174b59;
    --teal-light: #1d5a68;
    --teal-ring: #1a4f5d;
    --teal-disc: #133f4b;
    --lime: #6cc33a;
    --white: #ffffff;
    --muted: #8fa2a8;
    --rule: #a9b6ba;
  }
  * { margin: 0; padding: 0; box-sizing: border-box; }
  html, body {
    width: 1200px; height: 900px; overflow: hidden;
    background: var(--backdrop);
    font-family: "Montserrat", sans-serif;
  }
  .sheet { position: relative; width: 1200px; height: 900px; }
  .card {
    position: absolute; left: 320px; width: 560px; height: 320px;
    overflow: hidden;
    box-shadow: 0 18px 40px rgba(0,0,0,.45);
  }
  .brand {
    position: absolute; display: flex; align-items: center; gap: 10px;
  }
  .brand__dot { width: 14px; height: 14px; border-radius: 50%; background: var(--lime); flex: none; }
  .brand__name { color: var(--white); font-weight: 800; letter-spacing: 2px; line-height: 1; }

  /* ---------- front: contact side ---------- */
  .card--front {
    top: 100px;
    background: linear-gradient(135deg, var(--teal-deep) 0%, var(--teal-mid) 60%, var(--teal-light) 100%);
  }
  .edge-band { position: absolute; left: 0; top: 0; bottom: 0; width: 10px; }
  .edge-band__white { position: absolute; left: 0; top: 0; width: 10px; height: 62%; background: var(--white); }
  .edge-band__lime  { position: absolute; left: 0; top: 62%; width: 10px; height: 38%; background: var(--lime); }
  .hashtag {
    position: absolute; left: 30px; bottom: 38px;
    transform-origin: left bottom; transform: rotate(-90deg) translateY(100%);
    color: var(--lime); font-weight: 500; font-size: 15px; letter-spacing: .5px;
  }
  .card--front .brand { left: 66px; top: 126px; }
  .card--front .brand__name { font-size: 40px; }
  .divider {
    position: absolute; left: 250px; top: 60px; width: 1px; height: 200px;
    background: var(--rule); opacity: .7;
  }
  .contact { position: absolute; left: 274px; top: 70px; right: 20px; }
  .contact__name { color: var(--white); font-weight: 700; font-size: 20px; letter-spacing: 1px; }
  .contact__title { color: var(--white); font-size: 13px; margin-top: 2px; margin-bottom: 12px; }
  .contact__address { color: var(--muted); font-size: 12px; line-height: 1.45; margin-bottom: 10px; }
  .contact__line {
    display: flex; align-items: center; gap: 8px;
    color: var(--muted); font-size: 12px; line-height: 1.9;
  }
  .contact__line svg { width: 13px; height: 13px; flex: none; }

  /* ---------- back: brand side ---------- */
  .card--back {
    top: 480px;
    background: linear-gradient(135deg, var(--teal-deep) 0%, var(--teal-mid) 65%, var(--teal-light) 100%);
  }
  .backdrop-rings { position: absolute; inset: 0; width: 560px; height: 320px; }
  .card--back .brand { left: 0; right: 0; top: 92px; justify-content: center; }
  .card--back .brand__name { font-size: 44px; }
  .brand-sub {
    position: absolute; left: 0; right: 0; top: 160px; text-align: center;
    color: var(--white); font-weight: 800; font-size: 17px; letter-spacing: 3px;
  }
  .web {
    position: absolute; left: 0; right: 0; top: 200px; text-align: center;
    color: var(--white); font-size: 14px; letter-spacing: .5px;
  }
  .web strong { color: var(--lime); font-weight: 700; }
</style>
</head>
<body>
<main class="sheet">

  <section class="card card--front" aria-label="Business card, contact side">
    <div class="edge-band"><span class="edge-band__white"></span><span class="edge-band__lime"></span></div>
    <p class="hashtag">#ALLKAJU</p>
    <div class="brand"><span class="brand__dot"></span><span class="brand__name">KAJU</span></div>
    <span class="divider"></span>
    <div class="contact">
      <p class="contact__name">DANA WHITLOCK</p>
      <p class="contact__title">Chairman &amp; CEO</p>
      <p class="contact__address">4170 North Cinder Ridge<br>Road, Mesa, AZ 85201</p>
      <p class="contact__line">
        <svg viewBox="0 0 16 16" aria-hidden="true"><circle cx="8" cy="8" r="7" fill="none" stroke="#6cc33a" stroke-width="1.4"/><path d="M5.5 4.5l1.5 1.5-1 1c.6 1.2 1.6 2.2 2.8 2.8l1-1 1.5 1.5-1 1.2C7.5 11.3 4.7 8.5 4.5 5.5z" fill="#6cc33a"/></svg>
        480-555-0142
      </p>
      <p class="contact__line">
        <svg viewBox="0 0 16 16" aria-hidden="true"><rect x="1.5" y="3.5" width="13" height="9" fill="none" stroke="#6cc33a" stroke-width="1.4"/><path d="M1.5 3.5L8 9l6.5-5.5" fill="none" stroke="#6cc33a" stroke-width="1.4"/></svg>
        info@kajufreightco.example
      </p>
      <p class="contact__line">
        <svg viewBox="0 0 16 16" aria-hidden="true"><circle cx="8" cy="8" r="6.5" fill="none" stroke="#6cc33a" stroke-width="1.4"/><ellipse cx="8" cy="8" rx="3" ry="6.5" fill="none" stroke="#6cc33a" stroke-width="1.2"/><path d="M1.5 8h13" stroke="#6cc33a" stroke-width="1.2"/></svg>
        www.kajufreightco.example
      </p>
    </div>
  </section>

  <section class="card card--back" aria-label="Business card, brand side">
    <svg class="backdrop-rings" viewBox="0 0 560 320" aria-hidden="true">
      <circle cx="300" cy="150" r="250" fill="var(--teal-ring)" opacity=".45"/>
      <circle cx="290" cy="145" r="205" fill="var(--teal-disc)" opacity=".7"/>
      <circle cx="290" cy="145" r="205" fill="none" stroke="var(--teal-ring)" stroke-width="6"/>
    </svg>
    <div class="brand"><span class="brand__dot"></span><span class="brand__name">KAJU</span></div>
    <p class="brand-sub">FREIGHTWAYS</p>
    <p class="web">www.<strong>kajufreightco</strong>.example</p>
  </section>

</main>
</body>
</html>
```